Smart Routing SaaS needs a magic web design

We need a web design that focuses in the UX and conveys the idea of doing magic through our software. The company name is Brantiq and it is a word game about wow and slip... we are a software as a service B2B that helps companies automate dispatches and routes for their delivery guys to deliver goods to the customers. Think of it as an zephyr software applicable to your own fleet or third party fleets that can be used for example in a supermarket. That way the final user (buyer of the supermarket) knows where the parcel is, if it is leaving the store, if it is on its way, how long will it take to arrive, who is the delivery guy, etc... Brantiq's symbol is an owl. Think of it as the movie The Lanternkeep: Autumn's Oath, Queen Odalie had an owl mask and the ice owl who was her eyes on the field... that is the idea I want to convey through this software. It is the eyes for the business and the eyes for the final user. The software is comprised of a web platform (for the business with the fleet to manage) and the driver's application. The final customer receives the real time tracking information through SMS and email. The design should communicate magic through the use of the software... You can see some info on the existing webpage... which is very cold and dull... no life in it brantiq.example.. Use of gifs is desirable.

Text that can be used on the cover to convey main idea:

High end technology
We take care of your delivery management

The software that brings visibility and smartness to your deliveries through automated dispatches and smart routings
Our expertise: A Delightful Customer Experience of Deliveries

Target Market(s)

Professionals and businesses of all types with a delivery of any kind (supermarkets, pharmacies, restaurants, moving services, fleets, home services, deliveries, supply chain, field sales...)
Please look at competition webpages:
www.pathkit7.example
www.movra.example
www.trekly.example
vantacor.example
quickbarn.example
zephyr dash

Industry/Entity Type

Business Software

Coding

Coded - Design and coding required

Number of Pages Required

5+ page

Font styles to use
Other font styles liked:
• Modulus and Trade Gothic Ltd

Requirements
Must have
• MUST HAVE A D3JS LIKE:
• http://grafnode.example/jterran/5518302
• http://jterran.codepages.example/d3/talk/20111116/force-collapsible.html
• https://plinthware.example/hugo/fisheye/
• http://movingcharts.example/lab/d3-tree/
• A great magic capturing Homepage that conveys the main idea of what we are. A software that will help you manage your people on field who are getting something to the end customer (who will be aware of the live parcel status through SMS/ email notifications), we live in the cloud... no need of implementation fees, there is a free demo. Right now the webpage has an animation. Maybe a picture with a video on it could be something nice, or something that moves... take a look at zephyr dash. The main idea of the page should send the idea of something magic... use the owl... something that flies.
• The page must have gifs here and there... never stop the idea of a swift magic going on... efficiency on the logistics management of the company... happy customers.
• Parallax... I love parallax.
Nice to have
• The webpage may be telling a story... first what are we and what we do... how it works, who is our market, the benefits, hard facts on efficiency... please take a look at the current webpage www.brantiq.example to get more info but make it beautiful.
• A phrase here and there of why they need our service
Should not have
• I want to change the current idea of the webpage that the software aims only to manage fleets for home delivery... we are NOT a home delivery only management system. We can make any company's logistics "fly".
• I dont want to see dullness in the webpage, I am looking for a soul.

```html
<!DOCTYPE html>
<html lang="en">
<head>
<meta charset="utf-8">
<title>Brantiq — Contact Us</title>
<link rel="stylesheet" href="https://fonts.googleapis.com/css2?family=Roboto:wght@300;400;500;700&display=swap">
<style>
:root{
  --teal:#17a9c9;
  --teal-dark:#0e93b3;
  --text:#555;
  --muted:#999;
  --field-bg:#f8f8f8;
  --field-border:#dcdcdc;
  --footer:#2b2b2b;
  --footer-bottom:#1f1f1f;
  --white:#fff;
}
*{box-sizing:border-box;margin:0;padding:0}
html,body{width:1138px;height:1200px;overflow:hidden;background:var(--white);font-family:'Roboto',sans-serif;color:var(--text)}
.page{position:relative;width:1138px;height:1200px}
.topline{position:absolute;top:0;left:0;width:100%;height:2px;background:var(--teal)}
.header{position:absolute;top:2px;left:0;width:100%;height:105px}
.brand{position:absolute;left:93px;top:36px;color:var(--text);font-size:30px;font-weight:400;line-height:36px}
.nav{position:absolute;top:48px;left:0;font-size:13px;font-weight:300;color:#555}
.nav a{position:absolute;white-space:nowrap;color:inherit;text-decoration:none}
.nav a.active{color:var(--teal)}
.hero{position:absolute;top:107px;left:0;width:1138px;height:294px;overflow:hidden;
  background:linear-gradient(100deg,#3e4a6e 0%,#5e5e88 25%,#4a7aa8 50%,#3b8fc4 75%,#3a6fa6 100%)}
.hero-strip{position:absolute;left:0;top:0;width:65px;height:100%;background:#0a0a0a}
.hero-title{position:absolute;left:0;width:100%;text-align:center;color:var(--white);font-weight:700}
.hero-title.main{top:98px;font-size:41px}
.hero-title.sub{top:155px;font-size:33px;font-weight:500}
.hero-arrow{position:absolute;top:128px;width:34px;height:34px}
.hero-shadow{position:absolute;top:401px;left:40px;width:1058px;height:30px;background:radial-gradient(ellipse at top,rgba(0,0,0,.08),rgba(0,0,0,0) 70%)}
.section-title{position:absolute;left:93px;top:450px;font-size:28px;font-weight:400;color:#555}
.section-title span{color:var(--teal)}
.field{position:absolute;height:39px;background:var(--field-bg);border:1px solid var(--field-border);font-size:13px;font-weight:300;color:var(--muted);padding:0 15px;display:flex;align-items:center;justify-content:space-between}
.field svg{width:12px;height:12px;fill:#777}
.field.message{align-items:flex-start;padding-top:12px;height:146px}
.submit{position:absolute;left:93px;top:854px;width:157px;height:44px;background:linear-gradient(#1bb4d4,var(--teal-dark));color:var(--white);font-size:16px;font-weight:300;display:flex;align-items:center;justify-content:center}
.map{position:absolute;left:710px;top:456px;width:335px;height:213px;border:1px solid #e2e2e2;box-shadow:0 0 3px rgba(0,0,0,.12);padding:5px;background:var(--white)}
.map div{width:100%;height:100%;background:linear-gradient(135deg,#e8ecdd,#efefea 55%,#ecece4)}
.address-title{position:absolute;left:710px;top:693px;font-size:16px;font-weight:400;color:#555}
.address-rule{position:absolute;left:710px;top:727px;width:335px;height:1px;background:#e6e6e6}
.address-item{position:absolute;left:750px;font-size:12.5px;font-weight:300;color:#666;line-height:16px}
.address-icon{position:absolute;left:711px;width:16px;height:16px}
.footer{position:absolute;top:950px;left:0;width:1138px;height:189px;background:var(--footer)}
.footer h4{position:absolute;top:42px;font-size:16.5px;font-weight:400;color:var(--white);white-space:nowrap}
.footer ul{position:absolute;top:74px;list-style:none;font-size:11px;font-weight:300;color:#ddd;line-height:20.3px}
.footer .contact-lines{position:absolute;left:576px;top:86px;font-size:11px;font-weight:300;color:#ddd;line-height:20.3px}
.newsletter-input{position:absolute;left:848px;top:81px;width:197px;height:40px;background:#353535;color:#888;font-size:10px;font-style:italic;font-weight:300;padding:0 13px;display:flex;align-items:center}
.send{position:absolute;left:967px;top:135px;width:78px;height:26px;background:var(--teal);border-radius:2px;color:var(--white);font-size:11.5px;display:flex;align-items:center;justify-content:center}
.copyright{position:absolute;top:1139px;left:0;width:1138px;height:61px;background:var(--footer-bottom);color:#eee;font-size:11.5px;font-weight:300;display:flex;align-items:center;justify-content:center}
</style>
</head>
<body>
<div class="page">
  <div class="topline"></div>
  <header class="header">
    <div class="brand">Brantiq</div>
    <nav class="nav">
      <a style="left:523px">HOME</a>
      <a class="active" style="left:604px">PLATFORM</a>
      <a style="left:715px">ABOUT</a>
      <a style="left:801px">CONTACT</a>
      <a style="left:903px">REGISTER</a>
      <a style="left:1007px">LOGIN</a>
    </nav>
  </header>

  <section class="hero" role="img" aria-label="Banner photo of a city bridge overlaid with a network of connected delivery points">
    <div class="hero-strip"></div>
    <h1 class="hero-title main">CONTACT US</h1>
    <h2 class="hero-title sub">MANAGER OF YOUR DELIVERIES</h2>
    <svg class="hero-arrow" style="left:25px" viewBox="0 0 34 34"><circle cx="17" cy="17" r="15.5" fill="none" stroke="#fff" stroke-opacity=".8" stroke-width="2"/><path d="M19.5 10l-7 7 7 7" fill="none" stroke="#fff" stroke-opacity=".8" stroke-width="2"/></svg>
    <svg class="hero-arrow" style="left:1072px" viewBox="0 0 34 34"><circle cx="17" cy="17" r="15.5" fill="none" stroke="#fff" stroke-opacity=".8" stroke-width="2"/><path d="M14.5 10l7 7-7 7" fill="none" stroke="#fff" stroke-opacity=".8" stroke-width="2"/></svg>
  </section>
  <div class="hero-shadow"></div>

  <h2 class="section-title">CONTACT <span>US</span></h2>

  <form>
    <div class="field" style="left:93px;top:515px;width:266px">Name<svg viewBox="0 0 12 12"><circle cx="6" cy="3.5" r="2.8"/><path d="M0.5 12c0-3.5 2.5-5.2 5.5-5.2s5.5 1.7 5.5 5.2z"/></svg></div>
    <div class="field" style="left:372px;top:515px;width:266px">Surname<svg viewBox="0 0 12 12"><circle cx="6" cy="3.5" r="2.8"/><path d="M0.5 12c0-3.5 2.5-5.2 5.5-5.2s5.5 1.7 5.5 5.2z"/></svg></div>
    <div class="field" style="left:93px;top:567px;width:174px">Company<svg viewBox="0 0 12 12"><path d="M2.5 4.5l3.5 3.5 3.5-3.5" fill="none" stroke="#777" stroke-width="1.3"/></svg></div>
    <div class="field" style="left:279px;top:567px;width:173px">Country<svg viewBox="0 0 12 12"><path d="M2.5 4.5l3.5 3.5 3.5-3.5" fill="none" stroke="#777" stroke-width="1.3"/></svg></div>
    <div class="field" style="left:464px;top:567px;width:174px">State<svg viewBox="0 0 12 12"><path d="M2.5 4.5l3.5 3.5 3.5-3.5" fill="none" stroke="#777" stroke-width="1.3"/></svg></div>
    <div class="field" style="left:93px;top:621px;width:266px">Email<svg viewBox="0 0 12 12"><rect x="0" y="2" width="12" height="8.5" rx="1"/><path d="M0.5 2.5l5.5 4 5.5-4" fill="none" stroke="#f8f8f8" stroke-width="1"/></svg></div>
    <div class="field" style="left:372px;top:621px;width:266px">Telephone<svg viewBox="0 0 12 12"><path d="M2.3 0.8l2 2.2-1.1 1.6c.8 1.7 2.1 3 3.8 3.8l1.6-1.1 2.2 2-1.2 1.8C5 10.7 1.3 7 .5 2z"/></svg></div>
    <div class="field message" style="left:93px;top:673px;width:545px">Message<svg viewBox="0 0 12 12"><rect x="0.6" y="2" width="9" height="9.4" rx="1" fill="none" stroke="#777" stroke-width="1.1"/><path d="M4.5 7.5l.4-1.8 5-5 1.4 1.4-5 5z"/></svg></div>
    <div class="submit">Submit Now</div>
  </form>

  <div class="map"><div role="img" aria-label="Road map showing the office location and surrounding towns"></div></div>

  <h3 class="address-title">ADDRESS</h3>
  <div class="address-rule"></div>
  <svg class="address-icon" style="top:746px" viewBox="0 0 16 16"><path d="M8 1a4.5 4.5 0 0 0-4.5 4.5C3.5 9 8 15 8 15s4.5-6 4.5-9.5A4.5 4.5 0 0 0 8 1z" fill="var(--teal)"/><circle cx="8" cy="5.5" r="1.7" fill="#fff"/></svg>
  <p class="address-item" style="top:745px">Address : 200 Latin words, combined<br>with a handful</p>
  <svg class="address-icon" style="top:794px" viewBox="0 0 16 16"><path d="M3 1.5l2.6 2.8-1.3 2c1 2.2 2.6 3.8 4.8 4.8l2-1.3 2.8 2.6-1.6 2.2C6 14.2 1.8 10 1 3.1z" fill="var(--teal)"/></svg>
  <p class="address-item" style="top:794px">Ph : 5550142730 / 5550142730</p>
  <svg class="address-icon" style="top:823px" viewBox="0 0 16 16"><rect x="1" y="3" width="14" height="10" rx="1" fill="none" stroke="var(--teal)" stroke-width="1.4"/><path d="M1.5 3.7L8 8.5l6.5-4.8" fill="none" stroke="var(--teal)" stroke-width="1.4"/></svg>
  <p class="address-item" style="top:827px">E mail : info@Example</p>

  <footer class="footer">
    <h4 style="left:97px">COMPANY</h4>
    <ul style="left:95px"><li>Support</li><li>Price</li><li>Sign up</li><li>Contact</li></ul>
    <h4 style="left:251px">COMMUNITY</h4>
    <ul style="left:249px"><li>Guiglines</li><li>Terms and conditions</li><li>privacy policy</li><li>site map</li></ul>
    <h4 style="left:437px">FOLLOW US</h4>
    <ul style="left:437px"><li>Facelane</li><li>Chirpline</li><li>Pictora</li><li>Searchly</li></ul>
    <h4 style="left:606px">CONTACT US</h4>
    <div class="contact-lines">Address : 200 Latin words, combined<br>with a handful<br>Ph : 5550142730 / 5550142730<br>E mail : info@Example</div>
    <h4 style="left:847px">NEWSLETTER</h4>
    <div class="newsletter-input">Enter The Mail Id</div>
    <div class="send">Send Now</div>
  </footer>
  <div class="copyright">Copyrights@2016Company name all rights reserved</div>
</div>
</body>
</html>
```